Business card design Needed for new logo / Construction business, home extensions and new builds

We need a business card design using our new logo files which i will attach to this project :)

We are a small construction business specialising in home extensions, new builds and property development. We are very ambitious and would appreciate professional and elegant designs for our new business card.

Very serious about using the services on MakerQuarry and recently acquired our new logo from here :)

Please get involved, i will feedback when i can as i am very busy but can respond daily, thanks

Target Market(s)

People that want to build onto their houses, new building developments or adding too their existing property

Industry/Entity Type

Construction

Contact Information for Business Card

Renwick Tolliver Construction, Lionel Ashby (Managing Director), Tel 07822254961, email - info@renwick-tolliver, www.renwick-tolliver.co.uk

Colors

Designer to choose colors to be used in the design.

Requirements
Must have
• I like a deep grey on the back please. A lot of you have provided black from and back, try mixing things up a little. The black looks cool 😎 Thanks

```html
<!DOCTYPE html>
<html lang="en">
<head>
<meta charset="utf-8">
<title>Renwick Tolliver Construction – Business Card</title>
<link href="https://fonts.googleapis.com/css2?family=Open+Sans:wght@400;600;700&display=swap" rel="stylesheet">
<style>
  :root {
    --backdrop: #222223;
    --card-front: #18181a;
    --card-back: #1f1f23;
    --gold: #e0a12c;
    --gold-light: #f3cf6e;
    --gold-dark: #a9731a;
    --silver: #c9cacc;
    --white: #f4f4f4;
    --emboss: #2a2a2e;
    --faint: #2b2b30;
  }
  * { margin: 0; padding: 0; box-sizing: border-box; }
  html, body {
    width: 1200px; height: 780px; overflow: hidden;
    background: var(--backdrop);
    font-family: "Open Sans", Arial, sans-serif;
  }
  .canvas { position: relative; width: 1200px; height: 780px; }

  .card {
    position: absolute;
    width: 560px; height: 320px;
    overflow: hidden;
    box-shadow: 0 14px 30px rgba(0,0,0,.55);
  }
  .card::after {
    content: ""; position: absolute; left: 0; right: 0; bottom: 0; height: 6px;
    background: linear-gradient(90deg, var(--gold-dark), var(--gold-light) 55%, var(--gold));
  }

  /* Front */
  .card--front { left: 60px; top: 70px; background: var(--card-front); }
  .brand {
    position: absolute; left: 0; right: 0; top: 120px;
    display: flex; align-items: center; justify-content: center; gap: 12px;
  }
  .brand__mark { width: 18px; height: 18px; background: var(--emboss); }
  .brand__name {
    color: var(--emboss); font-weight: 700; font-size: 26px;
    letter-spacing: 2px; text-transform: uppercase; line-height: 1.15; text-align: center;
  }

  /* Back */
  .card--back { left: 580px; top: 390px; background: var(--card-back); }
  .back__wordmark {
    position: absolute; left: 0; right: 0; bottom: 34px; text-align: center;
    color: var(--faint); font-weight: 700; font-size: 34px;
    letter-spacing: 3px; text-transform: uppercase; line-height: 1.1;
  }
  .person { position: absolute; left: 44px; top: 110px; }
  .person__name { font-size: 30px; font-weight: 700; line-height: 1.1; }
  .person__first { color: var(--silver); }
  .person__last { color: var(--gold); }
  .person__role { color: var(--white); font-size: 14px; margin-top: 4px; margin-left: 96px; }

  .divider {
    position: absolute; left: 300px; top: 78px; width: 2px; height: 118px;
    background: var(--white);
  }

  .contacts { position: absolute; left: 322px; top: 86px; list-style: none; }
  .contacts li {
    display: flex; align-items: center; gap: 9px;
    color: var(--white); font-size: 13px; line-height: 1; margin-bottom: 14px;
  }
  .contacts svg { width: 15px; height: 15px; flex: none; }

  .address {
    position: absolute; left: 0; right: 0; top: 222px; text-align: center;
    color: var(--white); font-size: 13px;
  }
</style>
</head>
<body>
<main class="canvas">

  <section class="card card--front" aria-label="Card front">
    <div class="brand">
      <span class="brand__mark"></span>
      <span class="brand__name">Renwick Tolliver<br>Construction</span>
    </div>
  </section>

  <section class="card card--back" aria-label="Card back">
    <div class="back__wordmark">Renwick Tolliver<br>Construction</div>

    <div class="person">
      <div class="person__name"><span class="person__first">Lionel</span> <span class="person__last">Ashby</span></div>
      <div class="person__role">Managing Director</div>
    </div>

    <div class="divider"></div>

    <ul class="contacts">
      <li>
        <svg viewBox="0 0 24 24" aria-hidden="true"><path fill="#e0a12c" d="M6.6 10.8a15.1 15.1 0 0 0 6.6 6.6l2.2-2.2c.3-.3.7-.4 1-.2 1.1.4 2.3.6 3.6.6.6 0 1 .4 1 1V20c0 .6-.4 1-1 1A17 17 0 0 1 3 4c0-.6.4-1 1-1h3.5c.6 0 1 .4 1 1 0 1.3.2 2.5.6 3.6.1.3 0 .7-.2 1z"/></svg>
        0782 225 4961
      </li>
      <li>
        <svg viewBox="0 0 24 24" aria-hidden="true"><rect x="2" y="5" width="20" height="14" rx="2" fill="#e0a12c"/><path d="M3 6l9 7 9-7" fill="none" stroke="#1f1f23" stroke-width="1.6"/></svg>
        info@renwick-tolliver.co.uk
      </li>
      <li>
        <svg viewBox="0 0 24 24" aria-hidden="true"><circle cx="12" cy="12" r="10" fill="#e0a12c"/><path d="M2 12h20M12 2c3 3 3 17 0 20M12 2c-3 3-3 17 0 20" fill="none" stroke="#1f1f23" stroke-width="1.4"/></svg>
        www.renwick-tolliver.co.uk
      </li>
    </ul>

    <p class="address">Hartwell Lane, Elmcroft Dorchester, DT4 7QL</p>
  </section>

</main>
</body>
</html>
```